Willow Cradle Pregnancy and Baby Massage

I need a web design for a new business, WILLOW CRADLE PREGNANCY AND BABY MASSAGE that I am in the process of setting up in the suburbs of Perth, Western Australia. The business is owned and operated by myself and my intention is to service Pregnant Mothers and Parents of Young Babies that would benefit from massage. I would like to have a "Home Page" and pages for "About Me", "Pregnancy Massage", "Baby Massage", a Pricing Page for Pregnancy Massage Sessions, a Pricing Page for Baby Massage Sessions, and a "Contact Me" page to allow clients to either contact me with queries or book available pregnancy massage sessions on a particular day of the week. I would also like a "News" page that would include articles I have written, news about new courses and a link to my Facebook page (yet to be set up). I would like to keep the colour schemes similar to my logo design colours. I need the design to be easy to follow and to appeal to a younger audience (20's to mid 30's).
The target audience is pregnant mothers-to-be wishing to receive massage treatments, and new parents and grandparents of small babies that would like to learn how to massage their babies.
The look and feel should be modern, professional, elegant and feminine.
I need the design to be in a standard format such that I can update the content by myself ( and does not need specialised software) as the company and business progresses.

Target Market(s)

Contact Information for Business Card

Card should have rounded edges. Design should have the same "feel" as the website. Contact Details of my business address, mobile phone, email and website should be included.

Font styles to use
Script

Requirements
Must have
• Same colours as logo design. In cmyk system, the colours are: 20,60,0,0 which best result is pantone 681 and 40,40,0,0 which best result is pantone 2645. Card should include the logo design.

```html
<!DOCTYPE html>
<html lang="en">
<head>
<meta charset="utf-8">
<title>Willow Cradle Pregnancy and Baby Massage</title>
<link rel="stylesheet" href="https://fonts.googleapis.com/css2?family=Lato:ital,wght@0,400;0,700;1,400&family=Source+Sans+3:wght@400;600&display=swap">
<style>
:root{
  --lilac:#8d80b8;
  --lilac-deep:#8a7fbd;
  --rose:#b5609b;
  --rose-band:#b7689f;
  --rose-soft:#c48ab8;
  --blush:#f7eff1;
  --blush-deep:#f1dfe5;
  --ink:#3d3b40;
  --grey:#555258;
  --white:#ffffff;
}
*{box-sizing:border-box;margin:0;padding:0}
html,body{width:1200px;height:2500px;overflow:hidden}
body{position:relative;background:var(--white);font-family:"Lato",sans-serif;color:var(--ink)}
.abs{position:absolute}
.heading{font-family:"Source Sans 3",sans-serif;font-weight:400}

/* top bar */
.topbar{left:0;top:0;width:1200px;height:40px;background:var(--lilac);color:var(--white);font-size:16px}
.topbar .item{position:absolute;top:0;height:40px;display:flex;align-items:center;gap:10px}

/* nav */
.nav{left:0;top:40px;width:1200px;height:115px;background:var(--white)}
.nav a{position:absolute;top:46px;font-size:20px;color:var(--ink);text-decoration:none}
.nav a.current{color:var(--rose)}
.brand{position:absolute;left:450px;top:28px;width:300px;text-align:center;color:var(--rose);font-size:19px;line-height:1.25;font-weight:700}
.brand-dot{display:block;width:16px;height:16px;border-radius:50%;background:var(--rose);margin:0 auto 5px}

/* hero */
.hero{left:0;top:155px;width:1200px;height:563px;background:linear-gradient(160deg,#fbf6f7 0%,var(--blush) 60%,var(--blush-deep) 100%)}
.hero-title{left:78px;top:318px;font-size:38px;color:var(--rose)}
.hero-sub{left:78px;top:376px;width:522px;text-align:right;font-size:23px;color:var(--rose)}
.hero-copy{left:78px;top:418px;width:460px;font-size:16.5px;line-height:24px;color:var(--ink)}
.btn{position:absolute;display:flex;align-items:center;justify-content:center;font-family:"Source Sans 3",sans-serif;font-size:20px;letter-spacing:.3px;text-transform:uppercase}
.btn.solid{background:var(--rose);color:var(--white)}
.btn.outline{border:2px solid var(--rose);color:var(--rose)}
.btn.outline-light{border:2px solid var(--white);color:var(--white)}

/* about */
.about{left:0;top:718px;width:1200px;height:292px;background:var(--rose-band);color:var(--white);text-align:center;border-bottom:3px dotted #e9cde0}
.about h2{position:absolute;left:0;top:36px;width:1200px;font-size:44px}
.about p{position:absolute;left:235px;top:94px;width:730px;font-size:15px;line-height:25px}

/* sessions */
.tab{top:1010px;width:226px;height:62px;background:var(--lilac-deep);color:var(--white);font-size:42px;display:flex;align-items:center;justify-content:center}
.session-title{width:360px;text-align:center;font-style:italic;font-size:23px;line-height:27px;color:var(--rose)}
.session-copy{font-size:15px;line-height:25px;color:var(--grey)}
.session-copy ul{list-style:none}
.session-copy li{position:relative;padding-left:18px}
.session-copy li::before{content:"";position:absolute;left:3px;top:10px;width:6px;height:6px;border-radius:50%;background:var(--grey)}
.benefits{left:433px;top:1010px;width:334px;height:718px;background:linear-gradient(180deg,#f6ecef 0%,#f3e2e8 100%);border:2px dotted #b9a9b4;box-shadow:0 2px 6px rgba(0,0,0,.18)}
.benefits h3{position:absolute;left:0;top:38px;width:100%;text-align:center;font-size:46px;color:var(--rose)}
.benefits .tag{position:absolute;left:0;top:95px;width:100%;text-align:center;font-size:24px;color:var(--grey)}
.benefits .lead{position:absolute;left:25px;top:312px;width:284px;text-align:center;font-style:italic;font-size:14px;line-height:25px;color:var(--grey)}
.benefits .session-copy{position:absolute;left:18px;top:430px;width:300px;font-size:14.5px;line-height:24px}

/* contact */
.contact-rule{left:88px;top:1804px;width:1024px;height:2px;background:#b3aabd}
.contact-title{left:420px;top:1776px;width:360px;height:60px;background:var(--white);display:flex;align-items:center;justify-content:center;gap:18px;color:var(--lilac-deep);font-size:46px}
.contact-title .dot{width:22px;height:22px;border-radius:50%;border:3px solid var(--rose)}
.field{border:1.5px solid var(--rose);font-size:15px;color:var(--grey);padding:10px 8px;background:var(--white)}
.send{left:675px;top:1993px;width:74px;height:74px;border-radius:50%;border:1.5px solid var(--rose);background:var(--white);display:flex;align-items:center;justify-content:center}
.contact-info{left:805px;top:1836px;width:340px;text-align:center;font-size:15.5px;line-height:25px;color:var(--grey)}
.contact-info h4{font-weight:400;font-size:21px;color:var(--rose);margin-bottom:10px}
.contact-info svg{display:block;margin:4px auto 2px}

/* footer */
.footer{left:0;top:2112px;width:1200px;height:335px;color:var(--white)}
.footer h5{position:absolute;top:45px;font-family:"Source Sans 3",sans-serif;font-weight:400;font-size:27px}
.quote{position:absolute;left:77px;width:333px;height:70px;background:rgba(255,255,255,.3);font-style:italic;font-size:14px;line-height:24px;padding:10px 12px}
.quote::after{content:"";position:absolute;right:22px;bottom:-12px;border-left:12px solid transparent;border-right:12px solid transparent;border-top:12px solid rgba(255,255,255,.3)}
.client{position:absolute;left:200px;width:175px;text-align:right;font-size:15px}
.tweet{position:absolute;left:433px;width:330px;font-size:15px;line-height:24px;padding-left:36px}
.tweet .mark{position:absolute;left:8px;top:6px;width:14px;height:14px;border-radius:50%;background:var(--white)}
.news-field{position:absolute;left:790px;width:332px;height:39px;background:rgba(255,255,255,.35);font-size:15px;padding:9px 12px}
.subscribe{position:absolute;left:880px;top:2312px;width:166px;height:40px;background:var(--lilac);border:2px solid var(--white);display:flex;align-items:center;justify-content:center;font-size:19px;font-family:"Source Sans 3",sans-serif}
.bottombar{left:0;top:2447px;width:1200px;height:53px;background:var(--lilac);color:var(--white);font-size:16px;display:flex;align-items:center;justify-content:center}
</style>
</head>
<body>

<header class="abs topbar">
  <div class="item" style="left:78px">
    <svg width="22" height="16" viewBox="0 0 22 16"><rect x="1" y="1" width="20" height="14" rx="2" fill="none" stroke="#fff" stroke-width="2"/><path d="M1 2l10 7 10-7" fill="none" stroke="#fff" stroke-width="2"/></svg>
    <span>maren.holloway@willow-cradle.com.au</span>
  </div>
  <div class="item" style="left:990px">
    <svg width="18" height="18" viewBox="0 0 24 24"><path d="M6.6 10.8a15 15 0 0 0 6.6 6.6l2.2-2.2a1 1 0 0 1 1-.25 11.4 11.4 0 0 0 3.6.57 1 1 0 0 1 1 1V20a1 1 0 0 1-1 1A17 17 0 0 1 3 4a1 1 0 0 1 1-1h3.5a1 1 0 0 1 1 1c0 1.25.2 2.45.57 3.6a1 1 0 0 1-.25 1z" fill="#fff"/></svg>
    <span>041 5550 372</span>
  </div>
</header>

<nav class="abs nav">
  <a class="current" style="left:78px">Home</a>
  <a style="left:167px">About Me</a>
  <a style="left:288px">benefits</a>
  <div class="brand"><span class="brand-dot"></span>Willow Cradle<br>Pregnancy and Baby Massage</div>
  <a style="left:790px">Sessions</a>
  <a style="left:910px">Testimonials</a>
  <a style="left:1055px">Contact</a>
</nav>

<section class="abs hero">
  <svg class="abs" style="left:610px;top:140px" width="560" height="420" viewBox="0 0 560 420">
    <circle cx="160" cy="158" r="150" fill="#8f82bd"/>
    <circle cx="160" cy="158" r="138" fill="none" stroke="#d8d0ea" stroke-width="1.5" stroke-dasharray="3 4"/>
    <circle cx="160" cy="158" r="128" fill="#fff"/>
    <circle cx="160" cy="158" r="120" fill="url(#skin)" role="img" aria-label="Photo of a pregnant woman receiving a shoulder massage"/>
    <circle cx="417" cy="267" r="137" fill="#8f82bd"/>
    <circle cx="417" cy="267" r="125" fill="none" stroke="#d8d0ea" stroke-width="1.5" stroke-dasharray="3 4"/>
    <circle cx="417" cy="267" r="116" fill="#fff"/>
    <circle cx="417" cy="267" r="108" fill="url(#wrap)" role="img" aria-label="Photo of two newborn babies wrapped in a soft pink blanket"/>
    <defs>
      <radialGradient id="skin" cx="45%" cy="40%" r="70%"><stop offset="0" stop-color="#e7c2ad"/><stop offset=".6" stop-color="#d6a28c"/><stop offset="1" stop-color="#efe6e6"/></radialGradient>
      <radialGradient id="wrap" cx="50%" cy="45%" r="65%"><stop offset="0" stop-color="#e6b4a4"/><stop offset=".7" stop-color="#c98575"/><stop offset="1" stop-color="#a9786e"/></radialGradient>
    </defs>
  </svg>
</section>
<h1 class="abs heading hero-title">professional massage service</h1>
<p class="abs heading hero-sub">to pregnant mothers and babies</p>
<p class="abs hero-copy">Willow Cradle Pregnancy and Baby Massage was launched in 2017, offering massage for pregnant women, and instruction of baby massage to parents, grandparents and carers.</p>
<span class="btn solid" style="left:78px;top:503px;width:185px;height:42px">Read More</span>

<section class="abs about">
  <h2 class="heading">About Me</h2>
  <p>Maren is a Practitioner of Pregnancy Massage, and a Paediatric Massage Consultant. She completed her training with Prenatal Touch Institute, and the Infant Touch Learning Network. The ITLN is endorsed by the National College of Birth Carers, The Southern Wellness Therapies Society, and accredited by the Guild of Bodywork Practitioners</p>
  <span class="btn outline-light" style="left:505px;top:199px;width:187px;height:40px">Read More</span>
</section>

<!-- Pregnancy massage session -->
<div class="abs heading tab" style="left:132px">Sessions</div>
<div class="abs session-title" style="left:63px;top:1088px">Pregnancy Massage<br>Session</div>
<svg class="abs" style="left:118px;top:1158px" width="250" height="250" viewBox="0 0 250 250">
  <circle cx="125" cy="125" r="120" fill="#8f82bd"/>
  <circle cx="125" cy="125" r="104" fill="#fff"/>
  <circle cx="125" cy="125" r="100" fill="#f4f1f8" role="img" aria-label="Line illustration of a pregnant woman in profile"/>
</svg>
<div class="abs session-copy" style="left:85px;top:1428px;width:318px;text-align:center">Each session begins with a consultation to assess any high-risk factors, and to review any changes the body has undergone since the last session. This way the massage can be given in a safe manner.<br>The side-lying position is used with pillows for support. This is a comfortable resting position, and minimises pressure on one...</div>
<span class="btn solid" style="left:153px;top:1643px;width:184px;height:44px">Read More</span>

<!-- Benefits -->
<section class="abs benefits">
  <h3 class="heading">Benefits</h3>
  <p class="tag heading">- Pregnancy Massage -</p>
  <svg class="abs" style="left:58px;top:133px" width="214" height="176" viewBox="0 0 214 176">
    <rect x="0" y="0" width="214" height="176" rx="80" fill="url(#belly)" role="img" aria-label="Photo of hands forming a heart shape on a pregnant belly"/>
    <defs><linearGradient id="belly" x1="0" y1="0" x2="0" y2="1"><stop offset="0" stop-color="#b06aa4"/><stop offset=".5" stop-color="#e4c2b6"/><stop offset="1" stop-color="#b06aa4"/></linearGradient></defs>
  </svg>
  <p class="lead">Pregnancy massage is the prenatal use of massage therapy to support the physiological, structural and emotional wellbeing of both mother and baby.</p>
  <div class="session-copy">
    Pregnancy Massage is a professional relaxation massage that:
    <ul style="margin-top:8px">
      <li style="margin-bottom:6px">Reduces anxiety caused by hormonal changes.</li>
      <li style="margin-bottom:6px">Improves circulation</li>
      <li>Relaxes tense muscle, tones loose muscle and increases muscle flexibility.</li>
    </ul>
  </div>
  <span class="btn outline" style="left:70px;top:638px;width:188px;height:42px">Read More</span>
</section>

<!-- Baby massage sessions -->
<div class="abs heading tab" style="left:845px">Sessions</div>
<div class="abs session-title" style="left:773px;top:1088px">Baby Massage<br>Sessions</div>
<svg class="abs" style="left:828px;top:1158px" width="250" height="250" viewBox="0 0 250 250">
  <circle cx="125" cy="125" r="120" fill="#8f82bd"/>
  <circle cx="125" cy="125" r="104" fill="#fff"/>
  <circle cx="125" cy="125" r="100" fill="#f4f1f8" role="img" aria-label="Line illustration of hands massaging a baby"/>
</svg>
<div class="abs session-copy" style="left:790px;top:1428px;width:370px">
  Introductory Baby Massage Course
  <p style="padding-left:35px">This class teaches parents and carers the brief basics of Baby massage so they can get started at home.</p>
  Included in this course:
  <ul>
    <li>Permission sequence</li>
    <li>When is the best time to massage your baby</li>
    <li>Permission sequence</li>
  </ul>
</div>
<span class="btn solid" style="left:863px;top:1643px;width:185px;height:44px">Read More</span>

<!-- Contact -->
<div class="abs contact-rule"></div>
<h2 class="abs heading contact-title"><span class="dot"></span>Contact Us<span class="dot"></span></h2>
<div class="abs field" style="left:77px;top:1888px;width:228px;height:40px">Name</div>
<div class="abs field" style="left:323px;top:1888px;width:229px;height:40px">E-mail</div>
<div class="abs field" style="left:570px;top:1888px;width:228px;height:40px">Phone</div>
<div class="abs field" style="left:77px;top:1947px;width:721px;height:83px">Mesage</div>
<div class="abs send">
  <svg width="30" height="22" viewBox="0 0 30 22"><rect x="0" y="0" width="30" height="22" rx="3" fill="#8f82bd"/><path d="M2 3l13 9 13-9" fill="none" stroke="#fff" stroke-width="2.5"/></svg>
</div>
<div class="abs contact-info">
  <h4>Contact Info</h4>
  <svg width="20" height="28" viewBox="0 0 20 28"><path d="M10 0a10 10 0 0 1 10 10c0 7-10 18-10 18S0 17 0 10A10 10 0 0 1 10 0z" fill="#8f82bd"/><circle cx="10" cy="10" r="4" fill="#fff"/></svg>
  Maren Holloway Willow Cradle Pregnancy<br>and Infant Massage
  <svg width="24" height="24" viewBox="0 0 24 24" style="margin-top:10px"><path d="M6.6 10.8a15 15 0 0 0 6.6 6.6l2.2-2.2a1 1 0 0 1 1-.25 11.4 11.4 0 0 0 3.6.57 1 1 0 0 1 1 1V20a1 1 0 0 1-1 1A17 17 0 0 1 3 4a1 1 0 0 1 1-1h3.5a1 1 0 0 1 1 1c0 1.25.2 2.45.57 3.6a1 1 0 0 1-.25 1z" fill="#8f82bd"/></svg>
  041 5550 372
  <svg width="26" height="20" viewBox="0 0 26 20" style="margin-top:10px"><rect x="1" y="1" width="24" height="18" rx="2" fill="none" stroke="#8f82bd" stroke-width="2"/><path d="M1 2l12 8 12-8" fill="none" stroke="#8f82bd" stroke-width="2"/></svg>
  maren.holloway@willow-cradle.com.au
</div>

<!-- Footer -->
<footer class="abs footer">
  <svg class="abs" style="left:0;top:0" width="1200" height="335" viewBox="0 0 1200 335">
    <defs><linearGradient id="foot" x1="0" y1="0" x2="1" y2="1"><stop offset="0" stop-color="#c07fb2"/><stop offset=".55" stop-color="#c993bd"/><stop offset="1" stop-color="#b97aa8"/></linearGradient></defs>
    <rect width="1200" height="335" fill="url(#foot)" role="img" aria-label="Soft tinted photo of a baby resting, used as background"/>
  </svg>
  <h5 style="left:77px">Testimonials</h5>
  <div class="quote" style="top:96px">Lorem Ipsum is simply dummy text of the printing and typesetting industry.</div>
  <div class="client" style="top:178px">Client Name</div>
  <div class="quote" style="top:211px">Lorem Ipsum is simply dummy text of the printing and typesetting industry.</div>
  <div class="client" style="top:293px">Client Name</div>

  <h5 style="left:433px">Recent Tweets</h5>
  <div class="tweet" style="top:92px"><span class="mark"></span>Lorem Ipsum is simply dummy text of the printing and typesetting industry.<br>1 hour ago</div>
  <div class="tweet" style="top:186px"><span class="mark"></span>Lorem Ipsum is simply dummy text of the printing and typesetting industry.<br>4 hour ago</div>

  <h5 style="left:790px">Newsletter</h5>
  <div class="news-field" style="top:96px">Name</div>
  <div class="news-field" style="top:148px">Email</div>
</footer>
<div class="subscribe" style="color:#fff">SUBSCRIBE</div>

<div class="abs bottombar">©Willow Cradle - 2017. All Rights Reserved.</div>

</body>
</html>
```